Website for "Bright Morrow Ltd" cleaning bsuiness

We require a website to expose our business to the local market. We want to provide background on who we are and what we do but in an easily digestible way. We clean domestic and commercial premises and want to provide a list of all of our services to potential customers. We operate out of Warrington in the UK.

We would like the website to be animated in some way so that the experience of using it is not dull or mundane. This website needs to be an extension of our company.

Target Market(s)

30 - 60 year olds for Domestic plus commercial clients

Industry/Entity Type

Cleaning Service

Coding

Coded - Design and coding required

Number of Pages Required

4 page

Font styles to use
Sans Serif

Colors
0455a3
3176b5
85acd3
cfdeed
ffffff
000000
1b1b1b
c8c8c8
757575

Requirements
Must have
• Logo which has been provided. Theme based around the logo and its colours. Simple layout to avoid confusion.
Nice to have
• Animations where possible to impress the customer.
Should not have
• any pictures of cleaning equipment, fairies, maids etc

```html
<!DOCTYPE html>
<html lang="en">
<head>
<meta charset="utf-8">
<title>Bright Morrow Ltd – Professional Cleaning Service</title>
<link rel="stylesheet" href="https://fonts.googleapis.com/css2?family=Raleway:wght@400;500;600;700&family=Arimo:wght@400;700&family=Dancing+Script:wght@600&display=swap">
<style>
:root{
  --blue-deep:#0455a3;
  --blue:#3176b5;
  --blue-soft:#85acd3;
  --blue-pale:#cfdeed;
  --white:#ffffff;
  --black:#000000;
  --ink:#1b1b1b;
  --line:#c8c8c8;
  --grey:#757575;
}
*{box-sizing:border-box;margin:0;padding:0}
html,body{width:1200px;height:2995px;overflow:hidden;background:var(--white)}
body{position:relative;font-family:'Arimo',Arial,sans-serif;color:var(--grey)}
.abs{position:absolute}
h2{font-family:'Raleway',sans-serif;font-weight:400;letter-spacing:.5px}
.accent{color:var(--blue-deep)}
.script{font-family:'Dancing Script',cursive;font-weight:600}

/* hero */
.hero{left:0;top:0;width:1200px;height:690px;
  background:linear-gradient(180deg,#eceeee 0%,#dcdedd 45%,#c9c5bf 75%,#b9b1a7 100%)}
.hero-photo{left:0;top:0;width:1200px;height:690px}
.nav{left:0;top:0;width:1200px;height:80px;border-bottom:1px solid rgba(120,120,120,.35)}
.nav a{position:absolute;top:30px;font-family:'Raleway',sans-serif;font-size:17px;font-weight:500;color:var(--ink);text-decoration:none}
.nav a.active{color:var(--blue-deep)}
.nav .underline{position:absolute;left:338px;top:76px;width:78px;height:3px;background:var(--blue-deep)}
.brand{left:0;top:250px;width:1200px;text-align:center;font-family:'Raleway',sans-serif;font-weight:700;font-size:78px;color:var(--blue-deep)}
.chevron{left:0;top:560px}

/* welcome */
.welcome h2{left:0;top:710px;width:1200px;text-align:center;font-size:41px;color:var(--ink)}
.welcome p{left:150px;width:900px;text-align:center;font-size:13px;line-height:27px}
.btn{display:block;background:var(--blue-deep);color:var(--white);font-family:'Arimo',sans-serif;font-size:20px;text-align:center;line-height:58px;text-decoration:none}

/* domestic */
.domestic-photo{left:460px;top:1040px;width:740px;height:450px;
  background:linear-gradient(135deg,#c2b39d 0%,#a89880 50%,#d7d4cf 75%,#8e8677 100%)}
.domestic-panel{left:0;top:1040px}
.band-title{font-size:41px;color:var(--ink)}
.band-title .light{color:var(--white)}
.band-sub{font-size:19px;color:var(--ink)}
.svc-list{list-style:none;color:var(--white);font-size:16px}
.svc-list li{position:relative;padding-left:30px;margin-bottom:11px}
.svc-list li::before{content:"";position:absolute;left:4px;top:5px;width:7px;height:7px;border-radius:50%;background:var(--white);box-shadow:0 0 0 3px rgba(255,255,255,.3)}
.svc-list .desc{display:block;font-size:14px;line-height:25px;margin-top:6px;color:var(--blue-pale)}

/* intro cards */
.card-img{width:230px;height:166px}
.card h3{position:absolute;font-family:'Raleway',sans-serif;font-weight:400;font-size:25px;color:var(--ink)}
.card p{position:absolute;width:290px;font-size:13.5px;line-height:26px}
.more{position:absolute;font-family:'Raleway',sans-serif;font-weight:700;font-size:15px;color:var(--blue-deep);text-decoration:none;letter-spacing:.3px}

/* commercial */
.commercial-photo{left:0;top:1786px;width:760px;height:394px;
  background:linear-gradient(160deg,#b9a58c 0%,#cdbba3 45%,#a99275 100%)}
.commercial-panel{left:0;top:1786px}
.right-list{list-style:none;color:var(--white);text-align:right;font-size:16px}
.right-list li{position:relative;padding-right:30px;margin-bottom:11px}
.right-list li::after{content:"";position:absolute;right:6px;top:5px;width:7px;height:7px;border-radius:50%;background:var(--white);box-shadow:0 0 0 3px rgba(255,255,255,.3)}
.right-list .desc{display:block;font-size:14px;line-height:25px;margin-top:6px;color:var(--blue-pale)}

/* testimonial */
.testimonial h2{left:0;top:2240px;width:1200px;text-align:center;font-size:41px;color:var(--ink)}
.avatar{left:545px;top:2312px;width:110px;height:110px;border-radius:50%;border:3px solid var(--line);
  background:radial-gradient(circle at 50% 45%,#e8d2bf 0%,#d7b89c 55%,#b9976f 100%)}
.arrow-btn{width:44px;height:44px;border-radius:50%;border:1px solid var(--line)}
.quote{left:140px;top:2434px;width:920px;text-align:center;font-size:13.5px;line-height:28px}
.client{left:0;top:2506px;width:1200px;text-align:center;font-family:'Raleway',sans-serif;font-weight:700;font-size:18px;color:var(--blue-deep)}

/* footer */
.footer-bg{left:0;top:2580px;width:1200px;height:360px;
  background:linear-gradient(180deg,#f4f2f1 0%,#ece6e2 50%,#f3f3f3 100%)}
.footer-chevron{left:0;top:2580px}
.foot-brand{left:80px;top:2760px;width:230px;font-family:'Raleway',sans-serif;font-weight:700;font-size:34px;line-height:40px;color:var(--blue-deep)}
.foot-col h4{position:absolute;font-family:'Raleway',sans-serif;font-weight:700;font-size:17px;color:var(--blue-deep);letter-spacing:.4px}
.links{list-style:none;font-size:14px;color:var(--ink)}
.links li{position:relative;padding-left:24px;margin-bottom:12px}
.links li::before{content:"";position:absolute;left:0;top:3px;width:9px;height:9px;border:1.5px solid var(--blue-deep)}
.links li.on::before{background:var(--blue-deep)}
.contact-row{position:absolute;font-size:14px;line-height:25px;color:var(--ink)}
.contact-row svg{position:absolute;left:-40px;top:2px}
.news p{position:absolute;font-size:14px;line-height:25px;color:var(--ink);width:260px}
.field{left:874px;top:2815px;width:250px;height:40px;border:1px solid var(--line);background:var(--white);font-size:13px;color:var(--grey);padding:12px 10px}
.bottom-bar{left:0;top:2940px;width:1200px;height:55px;background:var(--blue-deep);color:var(--blue-pale);text-align:center;font-size:13.5px;line-height:55px}
.bottom-bar b{color:var(--white)}
</style>
</head>
<body>

<!-- hero -->
<section class="hero abs">
  <div class="hero-photo abs" role="img" aria-label="Softly blurred home interior with a vacuum cleaner on a wooden floor"></div>
  <nav class="nav abs">
    <a class="active" style="left:350px">HOME</a>
    <a style="left:471px">ABOUT US</a>
    <a style="left:606px">SERVICES</a>
    <a style="left:739px">BLOG</a>
    <a style="left:831px">CONTACT US</a>
    <span class="underline"></span>
  </nav>
  <div class="brand abs">Bright Morrow Ltd</div>
</section>
<svg class="chevron abs" width="1200" height="140" viewBox="0 0 1200 140">
  <polygon points="0,130 600,16 1200,130 1200,140 0,140" fill="var(--white)"/>
  <polyline points="0,126 600,12 1200,126" fill="none" stroke="var(--blue-deep)" stroke-width="9"/>
</svg>

<!-- welcome -->
<section class="welcome">
  <h2 class="abs">WELCOME TO <span class="accent">BRIGHT MORROW</span></h2>
  <p class="abs" style="top:776px">Lorem Ipsum is simply dummy text of the printing and typesetting industry. Lorem Ipsum has been the industry's standard dummy text ever since the 1500s, when an unknown printer took a galley of type and scrambled it to make a type specimen book.It has survived not only five centuries. Lorem Ipsum is simply dummy text of the printing and typesetting industry.</p>
  <p class="abs" style="top:858px">Lorem Ipsum is simply dummy text of the printing and typesetting industry. Lorem Ipsum has been the industry's standard dummy text ever since the 1500s, when an unknown printer took a galley of type and scrambled it to make a type specimen book.</p>
  <a class="btn abs" style="left:512px;top:922px;width:178px">KNOW MORE</a>
</section>

<!-- domestic services -->
<section class="domestic">
  <div class="domestic-photo abs" role="img" aria-label="Folded shirts beside a steam iron on a pale wooden table"></div>
  <svg class="domestic-panel abs" width="730" height="450" viewBox="0 0 730 450">
    <polygon points="0,0 722,0 472,450 0,450" fill="var(--blue)"/>
  </svg>
  <h2 class="band-title abs" style="left:76px;top:1090px">DOMESTIC <span class="light">SERVICES :</span></h2>
  <div class="band-sub script abs" style="left:78px;top:1148px">Weekly, fortnightly, monthly and adhoc cleans available</div>
  <ul class="svc-list abs" style="left:76px;top:1198px;width:540px">
    <li>Ironing<span class="desc">Lorem Ipsum is simply dummy text of the printing and typesetting industry.<br>Lorem Ipsum has been the industry's standard.</span></li>
    <li>Carpet Cleaning</li>
    <li>Tiled floor steam clean</li>
    <li>End of tenancy clean</li>
    <li>New house pre moving in clean</li>
    <li>Emergency requested clean</li>
  </ul>
</section>

<!-- who / what -->
<section class="card">
  <div class="card-img abs" style="left:78px;top:1556px;background:linear-gradient(135deg,#e9e4de,#b89272 70%,#8a6143)" role="img" aria-label="Cleaner holding supplies in an empty room"></div>
  <h3 style="left:322px;top:1550px">Who We <span class="accent">Are ?</span></h3>
  <p style="left:326px;top:1590px">Lorem Ipsum is simply dummy text of the printing and typesetting industry. Lorem Ipsum has been the industry's standard dummy text ever since the.</p>
  <a class="more" style="left:326px;top:1704px">READ MORE... &#187;</a>

  <div class="card-img abs" style="left:612px;top:1556px;background:linear-gradient(135deg,#f2f2ef,#dcdcd6 60%,#b9b7ac)" role="img" aria-label="Person vacuuming a bright living room"></div>
  <h3 style="left:856px;top:1550px">What We <span class="accent">Do ?</span></h3>
  <p style="left:860px;top:1590px">Lorem Ipsum is simply dummy text of the printing and typesetting industry. Lorem Ipsum has been the industry's standard dummy text ever since the.</p>
  <a class="more" style="left:860px;top:1704px">READ MORE... &#187;</a>
</section>

<!-- commercial cleaning -->
<section class="commercial">
  <div class="commercial-photo abs" role="img" aria-label="Floor scrubbing machine cleaning a tiled floor"></div>
  <svg class="commercial-panel abs" width="1200" height="394" viewBox="0 0 1200 394">
    <polygon points="488,0 1200,0 1200,394 722,394" fill="var(--blue)"/>
  </svg>
  <h2 class="band-title abs" style="left:600px;top:1836px;width:524px;text-align:right">COMMERCIAL <span class="light">CLEANING</span></h2>
  <div class="band-sub script abs" style="left:700px;top:1894px;width:424px;text-align:right">contract daily cleaning</div>
  <ul class="right-list abs" style="left:600px;top:1944px;width:524px">
    <li>Vacuuming<span class="desc">Lorem Ipsum is simply dummy text of the printing and typesetting industry.<br>Lorem Ipsum has been the industry's standard.</span></li>
    <li>Desk polishing</li>
    <li>Bin emptying</li>
    <li>Toilet cleaning</li>
  </ul>
</section>

<!-- testimonial -->
<section class="testimonial">
  <h2 class="abs">WHAT OUR <span class="accent">CLIENT SAY</span></h2>
  <div class="avatar abs" role="img" aria-label="Client portrait"></div>
  <svg class="arrow-btn abs" style="left:76px;top:2350px" viewBox="0 0 44 44"><polyline points="25,15 18,22 25,29" fill="none" stroke="var(--line)" stroke-width="2"/></svg>
  <svg class="arrow-btn abs" style="left:1080px;top:2350px" viewBox="0 0 44 44"><polyline points="19,15 26,22 19,29" fill="none" stroke="var(--line)" stroke-width="2"/></svg>
  <p class="quote abs">Lorem Ipsum is simply dummy text of the printing and typesetting industry. Lorem Ipsum has been the industry's standard dummy text ever since the 1500s, when an unknown printer took a galley&nbsp; tmake a type specimen book.</p>
  <div class="client abs">- CLIENT NAME</div>
</section>

<!-- footer -->
<footer>
  <div class="footer-bg abs" role="img" aria-label="Faint photo of a smiling woman lying on a soft carpet"></div>
  <svg class="footer-chevron abs" width="1200" height="120" viewBox="0 0 1200 120">
    <polygon points="0,0 1200,0 1200,112 600,8 0,112" fill="var(--white)"/>
    <polyline points="0,112 600,8 1200,112" fill="none" stroke="var(--blue-deep)" stroke-width="8"/>
  </svg>
  <div class="foot-brand abs">Bright Morrow Ltd</div>

  <div class="foot-col">
    <h4 style="left:354px;top:2702px">USEFULL LINKS</h4>
    <ul class="links abs" style="left:354px;top:2744px">
      <li class="on">Home</li><li>About Us</li><li>Services</li><li>Blog</li><li>Contact Us</li>
    </ul>

    <h4 style="left:608px;top:2702px">GET IN TOUCH</h4>
    <div class="contact-row" style="left:646px;top:2740px;width:200px">
      <svg width="24" height="22" viewBox="0 0 24 22"><polygon points="2,4 8,1 16,4 22,1 22,18 16,21 8,18 2,21" fill="none" stroke="var(--blue-deep)" stroke-width="1.6"/><line x1="8" y1="1" x2="8" y2="18" stroke="var(--blue-deep)" stroke-width="1.6"/><line x1="16" y1="4" x2="16" y2="21" stroke="var(--blue-deep)" stroke-width="1.6"/></svg>
      101- Lorem ipsum is simple dummy text of print and type setting industry
    </div>
    <div class="contact-row" style="left:646px;top:2830px">
      <svg width="22" height="22" viewBox="0 0 22 22"><path d="M4 2 L8 2 L10 7 L7.5 9 C9 12.5 10.5 14 13.5 15.5 L15.5 13 L20 15 L20 19 C20 20 19 21 18 21 C9 20 2 13 1.5 4 C1.5 3 2.5 2 4 2 Z" fill="none" stroke="var(--blue-deep)" stroke-width="1.6"/></svg>
      123 456 7890
    </div>
    <div class="contact-row" style="left:646px;top:2872px">
      <svg width="22" height="18" viewBox="0 0 22 18"><rect x="1" y="1" width="20" height="16" rx="2" fill="none" stroke="var(--blue-deep)" stroke-width="1.6"/><polyline points="1,3 11,10 21,3" fill="none" stroke="var(--blue-deep)" stroke-width="1.6"/></svg>
      info@brightmorrow.co.uk
    </div>

    <div class="news">
      <h4 style="left:876px;top:2702px">NEWSLETTER</h4>
      <p style="left:876px;top:2738px">Would you like to receive exclusive access to articles, white papers and our regular monthly newsletter?</p>
      <div class="field abs">Enter Email Id</div>
      <a class="btn abs" style="left:874px;top:2866px;width:156px;height:42px;line-height:42px;font-size:18px">SUBMIT</a>
    </div>
  </div>

  <div class="bottom-bar abs">© 2016 <b>Bright Morrow</b> - &nbsp;All rights reserved.</div>
</footer>

</body>
</html>
```